Automotive Business Card Design

I would just like a automotive themed card. nothing too extravagant, but catchy.

needs to say something about doing roadside assistance,mobile repairs, Diesel repairs, and Fleet maintenance

it can be single sided or double sided. no preference there.

Industry/Entity Type

Automotive

Contact Information for Business Card

Dean Marlowe
phone 534 861 2093
Name: Brightpath Automotive & Diesel Repair

```html
<!DOCTYPE html>
<html lang="en">
<head>
<meta charset="utf-8">
<title>Brightpath Automotive &amp; Diesel Repair – Business Card</title>
<link rel="stylesheet" href="https://fonts.googleapis.com/css2?family=Lato:wght@400;700&family=Playfair+Display+SC:wght@900&display=swap">
<style>
  :root {
    --page-bg: #e9e6e2;
    --card-white: #ffffff;
    --ink: #111111;
    --sky-top: #fbf3e4;
    --sky-mid: #f4c7a0;
    --horizon: #e8875a;
    --glow: #f0a266;
    --road-dark: #3a2a2a;
    --car-red: #c8231e;
    --shadow: rgba(0, 0, 0, 0.25);
  }

  html, body {
    margin: 0;
    padding: 0;
    width: 1200px;
    height: 425px;
    overflow: hidden;
    background: var(--page-bg);
  }

  .stage {
    position: relative;
    width: 1200px;
    height: 425px;
    display: flex;
    align-items: center;
    justify-content: center;
  }

  .business-card {
    position: relative;
    width: 700px;
    height: 400px;
    background: var(--card-white);
    overflow: hidden;
    box-shadow: 0 4px 14px var(--shadow);
  }

  .hero-photo {
    position: absolute;
    left: 0;
    top: 0;
    width: 100%;
    height: 82%;
    background:
      radial-gradient(ellipse 55% 30% at 62% 62%, var(--car-red) 0%, rgba(200, 35, 30, 0.6) 55%, rgba(200, 35, 30, 0) 100%),
      linear-gradient(180deg,
        var(--sky-top) 0%,
        var(--sky-top) 18%,
        var(--sky-mid) 42%,
        var(--glow) 55%,
        var(--horizon) 60%,
        var(--road-dark) 100%);
  }

  .company-name {
    position: absolute;
    left: 24px;
    top: 26px;
    margin: 0;
    font-family: "Playfair Display SC", serif;
    font-weight: 900;
    font-size: 27px;
    letter-spacing: 1px;
    color: var(--ink);
    white-space: nowrap;
  }

  .contact {
    position: absolute;
    right: 30px;
    top: 112px;
    text-align: left;
    font-family: "Lato", sans-serif;
    color: var(--ink);
  }

  .contact-name {
    margin: 0;
    font-size: 21px;
    font-weight: 400;
    letter-spacing: 0.5px;
    text-transform: uppercase;
  }

  .contact-phone {
    margin: 4px 0 0;
    font-size: 21px;
    letter-spacing: 1px;
    display: flex;
    align-items: center;
    gap: 8px;
  }

  .phone-icon {
    width: 14px;
    height: 14px;
  }

  .services {
    position: absolute;
    left: 0;
    bottom: 0;
    width: 100%;
    height: 18%;
    display: flex;
    flex-direction: column;
    align-items: center;
    justify-content: center;
    font-family: "Lato", sans-serif;
    font-weight: 400;
    font-size: 17px;
    letter-spacing: 2.5px;
    text-transform: uppercase;
    color: var(--ink);
    line-height: 1.25;
  }

  .services-line {
    margin: 0;
    white-space: nowrap;
  }
</style>
</head>
<body>
<main class="stage">
  <article class="business-card">
    <div class="hero-photo" role="img" aria-label="Photo of a red sports car with grey racing stripes on a wet road at sunset"></div>

    <h1 class="company-name">Brightpath Automotive &amp; Diesel Repair</h1>

    <div class="contact">
      <p class="contact-name">Dean Marlowe</p>
      <p class="contact-phone">
        <svg class="phone-icon" viewBox="0 0 14 14" aria-hidden="true">
          <rect x="0.75" y="0.75" width="12.5" height="12.5" fill="none" stroke="#111111" stroke-width="1.2"/>
        </svg>
        <span>534 861 2093</span>
      </p>
    </div>

    <section class="services" aria-label="Services">
      <p class="services-line">●Roadside Assistance,● Mobile Repairs,●</p>
      <p class="services-line">●Diesel Repairs,● Fleet Maintenance●</p>
    </section>
  </article>
</main>
</body>
</html>
```